Marlow Estate Fixers (Handyman / Home Improvement Company)

Looking for a double sided professional looking business card with Logo attached to be highlighted on one side and throwing in an image of a handyman as an option would be nice to see as well. We are a company focused on providing quality Handyman and Home improvement services in a timely manner that is done right the first time with integrity

Industry/Entity Type

Handyman / Home Improvement

Contact Information for Business Card

(LOGO, Name, Mobile and office phone numbers, email) on front side of card, (the words "The SOLUTION to all of your Handyman and Home Improvement needs" followed by "Family Owned and Operated" at the very bottom) on the back.

Colors
EB3D1F
EC4F4E
F09395
F8D3D4
FCEDEE

Requirements
Must have
• Red, Gray, Black Color scheme
Should not have
• No Yellow or Blue colors

```html
<!DOCTYPE html>
<html lang="en">
<head>
<meta charset="UTF-8">
<title>Marlow Estate Fixers – Business Card</title>
<link rel="stylesheet" href="https://fonts.googleapis.com/css2?family=Roboto:wght@400;500;700&family=Montserrat:wght@500;600;800&display=swap">
<style>
  :root {
    --bg: #d4d4d6;
    --card: #0d0d0d;
    --card-edge: #1a1a1a;
    --white: #f4f4f4;
    --red: #eb3d1f;
    --red-soft: #ec4f4e;
    --line: #c8261b;
  }
  * { box-sizing: border-box; margin: 0; padding: 0; }
  html, body {
    width: 1200px; height: 801px; overflow: hidden;
    background: radial-gradient(ellipse at 50% 40%, #e6e6e8 0%, var(--bg) 70%);
    font-family: "Roboto", Arial, sans-serif;
  }
  .stage {
    position: relative; width: 1200px; height: 801px;
    display: flex; align-items: center; justify-content: center; gap: 50px;
  }
  .card {
    position: relative; width: 540px; height: 309px;
    background: linear-gradient(160deg, var(--card-edge), var(--card) 60%);
    border-radius: 20px;
    box-shadow: 0 14px 30px rgba(0,0,0,.28);
    color: var(--white);
    overflow: hidden;
  }

  /* brand mark stand-in */
  .brand {
    display: flex; align-items: center; gap: 10px;
    font-family: "Montserrat", Arial, sans-serif;
    font-weight: 800; text-transform: uppercase;
    color: var(--white); line-height: 1.05;
  }
  .brand-dot { flex: none; border-radius: 50%; background: var(--red); }

  /* front side */
  .front .brand-area {
    position: absolute; left: 32px; top: 62px; width: 240px;
  }
  .front .brand { font-size: 24px; }
  .front .brand-dot { width: 34px; height: 34px; }
  .hours {
    position: absolute; left: 32px; bottom: 40px;
    font-family: "Montserrat", Arial, sans-serif; font-weight: 600;
    font-size: 11px; letter-spacing: 1.6px; text-transform: uppercase; line-height: 1.7;
  }
  .hours .closed { color: var(--red); }

  .contact {
    position: absolute; left: 300px; top: 44px; width: 210px;
  }
  .person-name { font-size: 25px; font-weight: 500; letter-spacing: -.2px; }
  .designation { color: var(--red); font-size: 11px; text-transform: uppercase; margin-top: 2px; }
  .rule { height: 1px; background: var(--line); margin: 12px 0; }
  .contact-list { list-style: none; font-size: 12px; line-height: 1; }
  .contact-list li { display: flex; align-items: center; gap: 9px; margin: 8px 0; }
  .contact-list svg { width: 13px; height: 13px; flex: none; fill: var(--red); }
  .address { font-size: 12px; line-height: 1.5; }

  /* back side */
  .back .brand-area {
    position: absolute; left: 0; right: 0; top: 70px;
    display: flex; justify-content: center;
  }
  .back .brand { font-size: 30px; }
  .back .brand-dot { width: 40px; height: 40px; }
  .tagline {
    position: absolute; left: 0; right: 0; bottom: 70px; text-align: center;
    font-family: "Montserrat", Arial, sans-serif; font-weight: 600;
    font-size: 10.5px; letter-spacing: 1.5px; text-transform: uppercase;
  }
  .family {
    position: absolute; left: 0; right: 0; bottom: 48px; text-align: center;
    font-family: "Montserrat", Arial, sans-serif; font-weight: 600;
    font-size: 10.5px; letter-spacing: 1.5px; text-transform: uppercase;
    color: var(--red);
  }
</style>
</head>
<body>
<main class="stage">

  <section class="card front" aria-label="Card front">
    <div class="brand-area">
      <div class="brand"><span class="brand-dot"></span><span>Marlow<br>Estate<br>Fixers</span></div>
    </div>
    <p class="hours">Opening hours - 9 am to 5 pm<br>Saturday Sunday - <span class="closed">Closed</span></p>

    <div class="contact">
      <h1 class="person-name">Daniel Marlow</h1>
      <p class="designation">Your designation</p>
      <div class="rule"></div>
      <ul class="contact-list">
        <li>
          <svg viewBox="0 0 24 24" aria-hidden="true"><path d="M6.6 10.8a15.1 15.1 0 0 0 6.6 6.6l2.2-2.2c.3-.3.7-.4 1-.2 1.1.4 2.3.6 3.6.6.6 0 1 .4 1 1V20c0 .6-.4 1-1 1A17 17 0 0 1 3 4c0-.6.4-1 1-1h3.5c.6 0 1 .4 1 1 0 1.3.2 2.5.6 3.6.1.3 0 .7-.2 1z"/></svg>
          555-214-3370 (Mobile)
        </li>
        <li>
          <svg viewBox="0 0 24 24" aria-hidden="true"><path d="M3 7c0-2 2-3 9-3s9 1 9 3v2h-5V7H8v2H3zM5 11h14l1 9H4zm4 2v2h2v-2zm4 0v2h2v-2zm-4 3v2h2v-2zm4 0v2h2v-2z"/></svg>
          555-214-3371 (Office)
        </li>
        <li>
          <svg viewBox="0 0 24 24" aria-hidden="true"><path d="M12 2a10 10 0 1 0 5 18.7l-1-1.7A8 8 0 1 1 20 12v1a2 2 0 0 1-4 0V7h-2v1a5 5 0 1 0 .7 7.3A4 4 0 0 0 22 13v-1A10 10 0 0 0 12 2zm0 13a3 3 0 1 1 0-6 3 3 0 0 1 0 6z"/></svg>
          info@marlowfixers.com
        </li>
      </ul>
      <div class="rule"></div>
      <p class="address">48 Harbor Lane, Portland,<br>OR 97201, USA</p>
    </div>
  </section>

  <section class="card back" aria-label="Card back">
    <div class="brand-area">
      <div class="brand"><span class="brand-dot"></span><span>Marlow<br>Estate Fixers</span></div>
    </div>
    <p class="tagline">Your solution to all of your handyman and home improvement needs</p>
    <p class="family">Family owned and operated</p>
  </section>

</main>
</body>
</html>
```